DuePath.com website design

We are a collection agency that collects debt from past residents of apartments on behalf of Property Management Companies. We are want to design a 3 page website with - Home - How it Works - Schedule Demo. We'd like a sketch of a skyline showing high rise apartment buildings, houses, shops, etc. We would like for there to be some animation, possibly clouds and the sun slowly moving. Maybe kids playing ball or catch or something like that. Bird flying and landing. An electric car charging (to indicate we are modern). We are looking for a friendly community vibe. The site will also need a button "Property Managers Login". When some comes to the site we would like a pop up that says "Property Managers Click Here/Past Residents Click Here" with a different icon for each that relates to the description. I've included a link to a test site we had designed so feel free to use some of the copy from it. We just aren't happy with the design. On the Home page our tag line should be "Get more payments, faster, from past residents!" and "Digital First, NOT Digital Only". All without transaction fees, we don't get paid unless we get you paid first!
Additional selling points:

24 hour virtual agent and virtual telephone agent so we don't miss any opportunities to GET YOUR MONEY!

Old school collection strategies meet cutting edge technology to create effective work flow algorithms to put the best debt collectors on your accounts with data driven intelligence to determine the best way to get paid.

No Subscription Fees
No Payment Processing Fees
No Software Fees
No Mail, Email or TXT Fees

Inquire about our FIRST PARTY accounts receivable outsourcing. You may qualify for free post move out A/R processing and AI payment negotiator for the low hanging fruit. Don't pay full collection commission when there wasn't a full collection attempt!

For the How it Works page - See the page from our previous design. I will include the link below. Please come up with your own version of this but you can use the copy from this page.

The schedule demo page will be a form that will feed to our CRM that will include:
Name
Email
Company
Title
Phone Number
Number of Units
Tell us how we can help you: (a box for them provide details)

Also include our phone number at the bottom with something like

Here is a link to our previous design test site:
https://brookpreview.net/duepath-new/
I've attached an image of the back end so you can get an idea of the colors we need, I've also included our logo. For the most part we would like most of the site to match the blue colors from our logo, but we do need to incorporate some of the yellow in the images I've attached. Possibly make the buttons on the site the yellow color? Make the sun Match the yellow? I'll leave it up to you.

```html
<!DOCTYPE html>
<html lang="en">
<head>
<meta charset="utf-8">
<title>DuePath – Home Page Design</title>
<link href="https://fonts.googleapis.com/css2?family=Oswald:wght@400;500;600&family=Roboto+Condensed:wght@400;700&family=Open+Sans:wght@400;600&display=swap" rel="stylesheet">
<style>
:root{
  --navy:#0f3d6b;
  --teal:#1bb8cb;
  --yellow:#fcc917;
  --slate:#53565a;
  --ink:#1a1a1a;
  --canvas:#c9c9c9;
  --field:#ffffff;
}
*{box-sizing:border-box;margin:0;padding:0}
html,body{width:855px;height:1200px;overflow:hidden;background:var(--canvas)}
body{position:relative;font-family:"Roboto Condensed",Arial,sans-serif;color:var(--ink)}
.frame{position:absolute;width:402px;height:1166px;overflow:hidden}
.frame--popup{left:15px;top:18px}
.frame--plain{left:434px;top:20px}
.page{position:absolute;left:0;top:0;width:764px;height:2216px;transform:scale(.5262);transform-origin:0 0;background:#fff;overflow:hidden}
.abs{position:absolute}
.brand{display:flex;align-items:center;gap:8px;font-family:"Oswald",sans-serif;font-weight:500;color:var(--navy);line-height:1;white-space:nowrap}
.brand__mark{background:var(--teal);border-radius:50%;flex:none}
.brand__sub{font-family:"Oswald",sans-serif;font-size:6px;letter-spacing:1.5px;color:var(--navy);white-space:nowrap}
/* header */
.header{top:0;left:0;width:764px;height:44px;background:#fff}
.nav{left:308px;top:0;width:456px;height:44px;background:var(--teal);clip-path:polygon(0 0,100% 0,100% 100%,24px 100%)}
.nav a{position:absolute;top:16px;font-size:10px;font-weight:700;color:#fff;text-decoration:none;white-space:nowrap}
.nav .demo{top:6px;height:32px;padding:0 14px;line-height:32px;background:var(--navy);border-radius:16px}
.nav .active-bar{position:absolute;left:36px;top:42px;width:32px;height:2px;background:var(--navy)}
/* hero */
.hero{top:44px;left:0;width:764px;height:559px;background:linear-gradient(#fff 0%,#fff 55%,#ececec 100%)}
.eyebrow{font-size:10px;color:#333}
.h1{font-family:"Oswald",sans-serif;font-weight:500;font-size:30px;line-height:35px;color:var(--navy);letter-spacing:.3px;white-space:nowrap;z-index:2}
.lead{font-size:9.5px;line-height:16px;color:#333}
.btn{display:inline-block;background:var(--yellow);color:#fff;font-family:"Oswald",sans-serif;font-weight:500;text-align:center;box-shadow:0 3px 6px rgba(0,0,0,.18);white-space:nowrap}
.btn-pill{border-radius:16px;font-family:"Roboto Condensed",sans-serif;font-weight:700;font-size:9px}
.cityscape{background:linear-gradient(160deg,#ffd85a 0%,#f29c3a 35%,#1d9ad6 65%,#0f4f9e 100%);border-radius:60px 20px 0 0;opacity:.9}
.h2{font-family:"Oswald",sans-serif;font-weight:500;font-size:22px;color:var(--navy);letter-spacing:.3px;white-space:nowrap}
.input{background:var(--field);border:1px solid #dedede;border-radius:3px;box-shadow:0 2px 4px rgba(0,0,0,.08);font-size:9px;color:#444;padding:13px 7px;width:205px;height:38px}
/* about */
.about-art{background:linear-gradient(180deg,#fff 0%,#fde6f0 30%,#ff6a8a 55%,#1d6fd6 80%,#fff 100%);box-shadow:0 2px 10px rgba(0,0,0,.25)}
.kicker{font-family:"Oswald",sans-serif;font-weight:400;font-size:18px;color:var(--teal);white-space:nowrap}
.kicker::after{content:"";display:inline-block;width:14px;height:3px;background:var(--teal);transform:rotate(40deg);margin-left:4px;vertical-align:middle}
.mega{font-family:"Oswald",sans-serif;font-weight:500;font-size:50px;color:var(--navy);line-height:1}
.copy{font-size:9px;line-height:16px;font-weight:700;color:#222;text-align:justify}
.copy--light{font-weight:400;color:#444}
/* feature bands */
.band{top:1093px;height:243px;width:254px;color:#fff}
.band h3{position:absolute;left:42px;top:85px;font-family:"Oswald",sans-serif;font-weight:400;font-size:18px;line-height:24px;white-space:nowrap}
.band .icon{position:absolute;left:42px;top:38px}
.ghost-btn{position:absolute;left:41px;top:174px;width:118px;height:36px;border:1.5px solid #fff;border-radius:3px;font-family:"Oswald",sans-serif;font-size:15px;text-align:center;line-height:33px}
/* columns */
.col .h2b{font-family:"Oswald",sans-serif;font-weight:500;font-size:26px;line-height:31px;color:var(--navy);white-space:nowrap}
.checks{list-style:none;font-size:12px;font-weight:700;line-height:20px;color:#222}
.checks li{display:flex;align-items:center;gap:5px}
.body12{font-size:12px;line-height:20px;font-weight:700;color:#222;text-align:justify;letter-spacing:.2px}
/* banner */
.banner{top:1700px;left:0;width:764px;height:226px;background:linear-gradient(135deg,#8aa0b6,#758da6)}
.banner p{position:absolute;left:0;width:764px;top:68px;text-align:center;font-family:"Oswald",sans-serif;font-size:26px;line-height:31px;color:#fff}
/* footer */
.contact{display:flex;gap:8px;font-size:8px;line-height:14px;color:#222}
.contact b{font-size:7px;color:var(--navy);display:block}
.dot{width:22px;height:22px;border-radius:50%;background:var(--navy);flex:none;display:flex;align-items:center;justify-content:center}
.footnav{top:2128px;left:0;width:764px;height:43px;background:var(--teal);display:flex;justify-content:center;gap:28px;align-items:center;font-size:10px;color:#fff}
.copyright{top:2171px;left:0;width:764px;height:45px;text-align:center;line-height:45px;font-size:9px;color:#222}
/* popup */
.overlay{left:0;top:0;width:764px;height:2216px;background:rgba(8,10,14,.8)}
.modal{left:63px;top:996px;width:638px;height:353px;background:#fff;border-radius:14px}
.modal .iconbox{background:linear-gradient(135deg,#1bb8cb,#0f3d6b);opacity:.25;border-radius:6px}
.modal .choice{position:absolute;top:176px;width:253px;height:42px;border-radius:7px;color:#fff;font-family:"Open Sans",sans-serif;font-weight:600;font-size:12.5px;text-align:center;line-height:42px}
.modal .choice u{text-underline-offset:2px}
.modal p{position:absolute;left:90px;top:236px;width:460px;text-align:center;font-family:"Open Sans",sans-serif;font-size:9px;line-height:16px;color:#222}
</style>
</head>
<body>

<!-- ============ Page with welcome popup ============ -->
<div class="frame frame--popup">
 <div class="page">
  <header class="abs header">
   <div class="abs brand" style="left:64px;top:8px;font-size:24px"><span class="brand__mark" style="width:24px;height:24px"></span>DuePath</div>
   <nav class="abs nav">
    <a style="left:36px">Home</a><a style="left:92px">How It Works</a><a style="left:180px">About Us</a><a style="left:250px">Contact</a><a class="demo" style="left:299px">Schedule Demo</a><span class="active-bar"></span>
   </nav>
  </header>
  <section class="abs hero">
   <div class="abs cityscape" role="img" aria-label="Colourful city skyline illustration with houses, towers, trees, cyclists and a balloon" style="left:420px;top:40px;width:344px;height:292px"></div>
   <div class="abs eyebrow" style="left:64px;top:64px">COMPLETE DEBT MANAGEMENT</div>
   <h1 class="abs h1" style="left:64px;top:82px">DUEPATH IS THE NEXT<br>GENERATION OF DEBT<br>RECOVERY MANAGEMENT</h1>
   <p class="abs lead" style="left:64px;top:194px;width:230px">Data driven intelligence meets unparalleled experience to deliver the most transparent, innovative and effective debt recovery.</p>
   <span class="abs btn btn-pill" style="left:62px;top:259px;width:90px;height:30px;line-height:30px">Get Started Now</span>
   <svg class="abs" style="left:0;top:340px" width="764" height="40"><path d="M0 4 H468 L478 38 H764" fill="none" stroke="var(--teal)" stroke-width="3"/></svg>
   <h2 class="abs h2" style="left:64px;top:350px">LET DUEPATH EARN YOUR BUSINESS</h2>
   <div class="abs input" style="left:62px;top:396px">Name</div><div class="abs input" style="left:278px;top:396px">Email</div><div class="abs input" style="left:495px;top:396px">Company</div>
   <div class="abs input" style="left:62px;top:446px">Title</div><div class="abs input" style="left:278px;top:446px">Phone Number</div><div class="abs input" style="left:495px;top:446px">Number of Units</div>
   <span class="abs btn" style="left:322px;top:497px;width:118px;height:37px;line-height:37px;font-size:15px">SUBMIT</span>
  </section>
  <section>
   <div class="abs about-art" role="img" aria-label="Colourful city illustration with balloons and sun" style="left:45px;top:667px;width:295px;height:380px"></div>
   <div class="abs kicker" style="left:394px;top:670px">About Us</div>
   <div class="abs mega" style="left:394px;top:698px">DuePath</div>
   <p class="abs copy" style="left:394px;top:760px;width:302px">Lorem ipsum dolor sit amet, consectetur adipiscing elit, sed do eiusmod tempor incididunt ut labore et dolore magna aliqua. Ut enim ad minim veniam, quis nostrud exercitation ullamco laboris nisi ut aliquip ex ea commodo consequat.</p>
   <p class="abs copy" style="left:394px;top:842px;width:302px">Lorem ipsum dolor sit amet, consectetur adipiscing elit, sed do eiusmod tempor incididunt ut labore et dolore magna aliqua. Ut enim ad minim veniam, quis nostrud exercitation ullamco laboris nisi ut aliquip ex ea commodo consequat.</p>
   <p class="abs copy copy--light" style="left:394px;top:924px;width:302px">Lorem ipsum dolor sit amet, consectetur adipiscing elit, sed do eiusmod tempor .</p>
   <span class="abs btn" style="left:394px;top:970px;width:118px;height:36px;line-height:36px;font-size:15px">READ MORE</span>
  </section>
  <section>
   <div class="abs band" style="left:0;background:var(--slate)"><h3>Transfer Accounts to<br>DuePath</h3><span class="ghost-btn">READ MORE</span></div>
   <div class="abs band" style="left:254px;background:var(--teal)"><h3>We contact your past<br>Resident Before They<br>are Delinquent</h3><span class="ghost-btn">READ MORE</span></div>
   <div class="abs band" style="left:508px;width:256px;background:var(--navy)"><h3>We offer Convenient<br>Payment platforms</h3><span class="ghost-btn">READ MORE</span></div>
  </section>
  <div class="abs overlay"></div>
  <div class="abs modal">
   <div class="abs brand" style="left:216px;top:14px;font-size:32px"><span class="brand__mark" style="width:34px;height:34px"></span>DuePath</div>
   <div class="abs brand__sub" style="left:320px;top:56px">DEBT RECOVERY MANAGEMENT</div>
   <div class="abs iconbox" role="img" aria-label="Icon of a hand holding money and a house" style="left:144px;top:96px;width:70px;height:68px"></div>
   <div class="abs iconbox" role="img" aria-label="Icon of apartment buildings" style="left:424px;top:96px;width:70px;height:68px"></div>
   <span class="choice" style="left:54px;background:var(--navy)">Property Managers <u>Click Here</u></span>
   <span class="choice" style="left:332px;background:var(--teal)">Past Residents <u>Click Here</u></span>
   <p>Nemo enim ipsam voluptatem quia voluptas sit aspernatur aut odit aut fugit, sed quia consequuntur magni dolores eos qui ratione voluptatem sequi nesciunt. Neque porro quisquam est, qui dolorem ipsum quia dolor sit amet, consectetur, adipisci velit, sed quia non numquam eius modi tempora incidunt ut labore et dolore magnam aliquam quaerat voluptatem.</p>
  </div>
 </div>
</div>

<!-- ============ Full home page ============ -->
<div class="frame frame--plain">
 <div class="page">
  <header class="abs header">
   <div class="abs brand" style="left:64px;top:8px;font-size:24px"><span class="brand__mark" style="width:24px;height:24px"></span>DuePath</div>
   <div class="abs brand__sub" style="left:140px;top:36px">DEBT RECOVERY MANAGEMENT</div>
   <nav class="abs nav">
    <a style="left:36px">Home</a><a style="left:92px">How It Works</a><a style="left:180px">About Us</a><a style="left:250px">Contact</a><a class="demo" style="left:299px">Schedule Demo</a><span class="active-bar"></span>
   </nav>
  </header>

  <section class="abs hero">
   <div class="abs cityscape" role="img" aria-label="Colourful city skyline illustration with houses, towers, trees, cyclists and a balloon" style="left:420px;top:40px;width:344px;height:292px"></div>
   <div class="abs eyebrow" style="left:64px;top:64px">COMPLETE DEBT MANAGEMENT</div>
   <h1 class="abs h1" style="left:64px;top:82px">DUEPATH IS THE NEXT<br>GENERATION OF DEBT<br>RECOVERY MANAGEMENT</h1>
   <p class="abs lead" style="left:64px;top:194px;width:230px">Data driven intelligence meets unparalleled experience to deliver the most transparent, innovative and effective debt recovery.</p>
   <span class="abs btn btn-pill" style="left:62px;top:259px;width:90px;height:30px;line-height:30px">Get Started Now</span>
   <svg class="abs" style="left:0;top:340px" width="764" height="40"><path d="M0 4 H468 L478 38 H764" fill="none" stroke="var(--teal)" stroke-width="3"/></svg>
   <h2 class="abs h2" style="left:64px;top:350px">LET DUEPATH EARN YOUR BUSINESS</h2>
   <div class="abs input" style="left:62px;top:396px">Name</div><div class="abs input" style="left:278px;top:396px">Email</div><div class="abs input" style="left:495px;top:396px">Company</div>
   <div class="abs input" style="left:62px;top:446px">Title</div><div class="abs input" style="left:278px;top:446px">Phone Number</div><div class="abs input" style="left:495px;top:446px">Number of Units</div>
   <span class="abs btn" style="left:322px;top:497px;width:118px;height:37px;line-height:37px;font-size:15px">SUBMIT</span>
  </section>

  <section>
   <div class="abs about-art" role="img" aria-label="Colourful city illustration with balloons and sun" style="left:45px;top:667px;width:295px;height:380px"></div>
   <div class="abs kicker" style="left:394px;top:670px">About Us</div>
   <div class="abs mega" style="left:394px;top:698px">DuePath</div>
   <p class="abs copy" style="left:394px;top:760px;width:302px">Lorem ipsum dolor sit amet, consectetur adipiscing elit, sed do eiusmod tempor incididunt ut labore et dolore magna aliqua. Ut enim ad minim veniam, quis nostrud exercitation ullamco laboris nisi ut aliquip ex ea commodo consequat.</p>
   <p class="abs copy" style="left:394px;top:842px;width:302px">Lorem ipsum dolor sit amet, consectetur adipiscing elit, sed do eiusmod tempor incididunt ut labore et dolore magna aliqua. Ut enim ad minim veniam, quis nostrud exercitation ullamco laboris nisi ut aliquip ex ea commodo consequat.</p>
   <p class="abs copy copy--light" style="left:394px;top:924px;width:302px">Lorem ipsum dolor sit amet, consectetur adipiscing elit, sed do eiusmod tempor .</p>
   <span class="abs btn" style="left:394px;top:970px;width:118px;height:36px;line-height:36px;font-size:15px">READ MORE</span>
  </section>

  <section>
   <div class="abs band" style="left:0;background:var(--slate)">
    <svg class="icon" width="54" height="36" viewBox="0 0 54 36" fill="none" stroke="#fff" stroke-width="2"><rect x="1" y="1" width="36" height="22" rx="2"/><path d="M7 9h18M7 15h12"/><path d="M32 32l14-14 5 5-14 14h-5z"/></svg>
    <h3>Transfer Accounts to<br>DuePath</h3><span class="ghost-btn">READ MORE</span></div>
   <div class="abs band" style="left:254px;background:var(--teal)">
    <svg class="icon" width="36" height="34" viewBox="0 0 36 34" fill="none" stroke="#fff" stroke-width="2"><rect x="2" y="8" width="14" height="24"/><rect x="16" y="2" width="14" height="30"/><path d="M6 14h6M6 20h6M20 8h6M20 14h6M20 20h6"/></svg>
    <h3>We contact your past<br>Resident Before They<br>are Delinquent</h3><span class="ghost-btn">READ MORE</span></div>
   <div class="abs band" style="left:508px;width:256px;background:var(--navy)">
    <svg class="icon" width="36" height="34" viewBox="0 0 36 34" fill="none" stroke="#fff" stroke-width="2"><path d="M4 10l18-8 4 8"/><rect x="2" y="10" width="30" height="22" rx="3"/><rect x="22" y="17" width="11" height="8" rx="2"/></svg>
    <h3>We offer Convenient<br>Payment platforms</h3><span class="ghost-btn">READ MORE</span></div>
  </section>

  <section class="col">
   <div class="abs kicker" style="left:80px;top:1394px">Old school collection strategies</div>
   <div class="abs h2b" style="left:78px;top:1424px">The best way to get<br>Paid</div>
   <ul class="abs checks" style="left:78px;top:1498px">
    <li><svg width="11" height="11" viewBox="0 0 11 11"><circle cx="5.5" cy="5.5" r="5.5" fill="var(--navy)"/><path d="M3 5.6l1.8 1.8L8 4" stroke="#fff" stroke-width="1.4" fill="none"/></svg>No Subscription Fees</li>
    <li><svg width="11" height="11" viewBox="0 0 11 11"><circle cx="5.5" cy="5.5" r="5.5" fill="var(--navy)"/><path d="M3 5.6l1.8 1.8L8 4" stroke="#fff" stroke-width="1.4" fill="none"/></svg>No Payment Processing Fees</li>
    <li><svg width="11" height="11" viewBox="0 0 11 11"><circle cx="5.5" cy="5.5" r="5.5" fill="var(--navy)"/><path d="M3 5.6l1.8 1.8L8 4" stroke="#fff" stroke-width="1.4" fill="none"/></svg>No Software Fees</li>
    <li><svg width="11" height="11" viewBox="0 0 11 11"><circle cx="5.5" cy="5.5" r="5.5" fill="var(--navy)"/><path d="M3 5.6l1.8 1.8L8 4" stroke="#fff" stroke-width="1.4" fill="none"/></svg>No Mail, Email or TXT Fees</li>
   </ul>
   <span class="abs btn" style="left:80px;top:1606px;width:118px;height:36px;line-height:36px;font-size:15px">READ MORE</span>

   <div class="abs kicker" style="left:394px;top:1394px">Digital First, NOT Digital Only</div>
   <div class="abs h2b" style="left:396px;top:1424px">We don't get paid unless<br>We get you paid first!</div>
   <p class="abs body12" style="left:398px;top:1498px;width:302px">Lorem ipsum dolor sit amet, consectetur adipiscing elit, sed do eiusmod tempor incididunt ut labore et dolore magna aliqua. Ut enim ad minim veniam, quis nostrud exercitation</p>
   <span class="abs btn" style="left:394px;top:1606px;width:118px;height:36px;line-height:36px;font-size:15px">READ MORE</span>
  </section>

  <section class="abs banner">
   <p>24 hour virtual agent and virtual telephone agent so<br>we don't miss any opportunities to</p>
   <span class="abs btn" style="left:316px;top:148px;width:132px;height:34px;line-height:34px;font-size:14px">GET YOUR MONEY!</span>
  </section>

  <footer>
   <div class="abs brand" style="left:240px;top:1966px;font-size:42px"><span class="brand__mark" style="width:44px;height:44px"></span>DuePath</div>
   <div class="abs brand__sub" style="left:384px;top:2024px;font-size:8px">DEBT RECOVERY MANAGEMENT</div>
   <div class="abs contact" style="left:78px;top:2080px"><span class="dot"><svg width="11" height="9" viewBox="0 0 11 9" fill="none" stroke="#fff"><rect x=".5" y=".5" width="10" height="8"/><path d="M.5 .5l5 4 5-4"/></svg></span><div><b>EMAIL</b>info@duepath.com</div></div>
   <div class="abs contact" style="left:288px;top:2080px"><span class="dot"><svg width="9" height="12" viewBox="0 0 9 12"><path d="M4.5 12C1 7 0 5.5 0 4.5a4.5 4.5 0 019 0c0 1-1 2.5-4.5 7.5z" fill="#fff"/><circle cx="4.5" cy="4.5" r="1.6" fill="var(--navy)"/></svg></span><div><b>OUR LOCATION</b>19 Nemo enim ipsam voluptatem<br>quia voluptas sit</div></div>
   <div class="abs contact" style="left:506px;top:2080px"><span class="dot"><svg width="11" height="11" viewBox="0 0 11 11"><path d="M2 .5l2 2.5-1 1.5c.8 1.6 1.9 2.7 3.5 3.5L8 7l2.5 2-1 1.5C5 10 1 6 .5 1.5z" fill="#fff"/></svg></span><div><b>PHONE NUMBER</b>+1 888-888-8888</div></div>
   <nav class="abs footnav"><span>Home</span><span>How It Works</span><span>About Us</span><span>Contact</span></nav>
   <div class="abs copyright">Copyright © 2022 DuePath - All Rights Reserved.</div>
  </footer>
 </div>
</div>

</body>
</html>
```